Torvane Email Signature Banners – Fabrication Capability Series

www.Torvane.com.au is an Australian engineering and fabrication company specialising in fabrication and welding of :
steel piping spools,
skids and frames,
small volume process steel tanks
and general steel fabrication
We require four distinct banner designs for use in Microsoft Lintaro email signatures. Each banner will highlight a specific capability while maintaining a consistent brand identity.
Deliverables
Four banners total:
Piping Spools Fabrication – focus on precision welding and stainless steel pipework
Skid & Frames Fabrication – highlight skid systems and structural frames
Small Steel Tanks Fabrication – show fabricated tanks and workshop craftsmanship
General Fabrication Solutions – broad steel fabrication theme for company-wide use
Dimensions: 600–700 px wide × 100 px high
Format: PNG (preferred), small file size prefered
Resolution: 72 dpi
Background: non-transparent, industrial or workshop setting
Text examples:
1. Piping Spools Fabrication
Option A: “Expert Fabrication Solutions for Process Piping”
Option B: “Precision Welding for Complex Systems”
Option C: “Delivering Quality in Every Spool”
Option D: “Engineered for Flow, Built for Strength”
2. Skid & Frames Fabrication
Option A: “Custom Engineered Modular Systems”
Option B: “Built Strong. Designed Smart.”
Option C: “Reliable Frames for Industrial Performance”
Option D: “Modular Fabrication for Seamless Integration”
3. Small Steel Tanks Fabrication
Option A: “Precision Built for Your Needs”
Option B: “Compact Strength. Proven Durability.”
Option C: “Fabricated for Performance and Longevity”
Option D: “Small Tanks. Big Reliability.”
4. General Fabrication Solutions
Option A: “Quality Craftsmanship, Proven Results”
Option B: “Your Partner in Precision Fabrication”
Option C: “Engineering Excellence in Every Weld”
Option D: “Australian Fabrication. Global Standards.”
Style Direction
Clean, professional, and engineering‑focused
Use Torvane brand colours
Blend photo realism with vector clarity (no heavy gradients)
Include subtle industrial textures or workshop imagery
Typography: bold sans‑serif, legible at small scale
Usage Context
These banners will appear at the bottom of staff email signatures via Lintaro Email Signature Tool for Microsoft 365, so clarity and fast loading are essential. No Logo is required in the banners.
Reference
Existing Torvane signature is attached. Colour palette to match the signature style and logo.
Target Market(s)
Engineering and construction companies,
Industry/Entity Type
Engineering fabrication design
Look and feel

```html
<!DOCTYPE html>
<html lang="en">
<head>
<meta charset="utf-8">
<title>Torvane Email Signature Banners</title>
<link rel="stylesheet" href="https://fonts.googleapis.com/css2?family=Teko:wght@500;600&family=Montserrat:wght@600&display=swap">
<style>
  :root {
    --canvas-bg: #333333;
    --brand-blue: #1757c0;
    --brand-blue-deep: #124aa8;
    --brand-sky: #1f8fe3;
    --brand-sky-deep: #1a7fd6;
    --white: #ffffff;
    --steel-light: #c9ced4;
    --steel-mid: #8f98a3;
    --steel-dark: #4d5661;
    --warm-glow: #e9c48a;
  }
  * { margin: 0; padding: 0; box-sizing: border-box; }
  html, body {
    width: 1200px; height: 754px; overflow: hidden;
    background: var(--canvas-bg);
  }
  .canvas { position: relative; width: 1200px; height: 754px; }
  .banner {
    position: absolute; left: 80px; width: 1040px; height: 148px;
    overflow: hidden;
  }
  .banner svg { position: absolute; inset: 0; display: block; }
  .banner--tanks { top: 89px; }
  .banner--general { top: 304px; }
  .banner--piping { top: 517px; }

  .kicker, .headline {
    position: absolute; color: var(--white); white-space: nowrap; line-height: 1;
  }
  .headline {
    font-family: "Teko", "Arial Narrow", sans-serif; font-weight: 600;
    text-transform: uppercase;
  }

  /* Small Steel Tanks */
  .banner--tanks .kicker {
    font-family: "Montserrat", Arial, sans-serif; font-weight: 600;
    font-size: 19.5px; letter-spacing: 0.5px;
    left: 0; right: 0; top: 29px; text-align: center;
  }
  .banner--tanks .headline {
    font-size: 61px; letter-spacing: 1px;
    left: 0; right: 0; top: 63px; text-align: center;
  }

  /* General Fabrication */
  .banner--general .kicker {
    font-family: "Teko", "Arial Narrow", sans-serif; font-weight: 500;
    font-size: 30px; letter-spacing: 0.5px; left: 53px; top: 20px;
  }
  .banner--general .headline {
    font-size: 78px; letter-spacing: 1px; left: 52px; top: 62px;
  }

  /* Piping Spools */
  .banner--piping .kicker {
    font-family: "Teko", "Arial Narrow", sans-serif; font-weight: 500;
    font-size: 32px; letter-spacing: 0.5px;
    left: 221px; width: 600px; top: 24px; text-align: center;
  }
  .banner--piping .headline {
    font-size: 78px; letter-spacing: 1px;
    left: 221px; width: 600px; top: 63px; text-align: center;
  }
</style>
</head>
<body>
<main class="canvas">

  <section class="banner banner--tanks" aria-label="Small Steel Tanks Fabrication banner">
    <svg viewBox="0 0 1040 148" width="1040" height="148" aria-hidden="true">
      <defs>
        <linearGradient id="tanks-bg" x1="0" y1="0" x2="1" y2="1">
          <stop offset="0" stop-color="var(--brand-blue)"/>
          <stop offset="1" stop-color="var(--brand-blue-deep)"/>
        </linearGradient>
      </defs>
      <rect class="banner-field" width="1040" height="148" fill="url(#tanks-bg)"/>
      <line class="kicker-rule" x1="184" y1="39" x2="303" y2="39" stroke="#ffffff" stroke-width="1.5"/>
      <line class="kicker-rule" x1="737" y1="39" x2="856" y2="39" stroke="#ffffff" stroke-width="1.5"/>
    </svg>
    <p class="kicker">SMALL STEEL TANKS FABRICATION</p>
    <h2 class="headline">Compact Strength. Proven Durability.</h2>
  </section>

  <section class="banner banner--general" aria-label="General Fabrication Solutions banner">
    <svg viewBox="0 0 1040 148" width="1040" height="148" aria-hidden="true">
      <defs>
        <linearGradient id="general-bg" x1="0" y1="0" x2="1" y2="1">
          <stop offset="0" stop-color="var(--brand-sky)"/>
          <stop offset="1" stop-color="var(--brand-sky-deep)"/>
        </linearGradient>
        <linearGradient id="coils-photo" x1="0" y1="0" x2="1" y2="1">
          <stop offset="0" stop-color="var(--warm-glow)"/>
          <stop offset="0.35" stop-color="var(--steel-light)"/>
          <stop offset="0.75" stop-color="var(--steel-mid)"/>
          <stop offset="1" stop-color="var(--steel-dark)"/>
        </linearGradient>
      </defs>
      <rect class="banner-field" width="1040" height="148" fill="url(#general-bg)"/>
      <polygon class="divider-stripe" points="680,0 690,0 663,148 653,148" fill="#ffffff"/>
      <polygon class="photo-area" points="697,0 1040,0 1040,148 670,148" fill="url(#coils-photo)"
               role="img" aria-label="Photo of rolled steel coils in a fabrication warehouse"/>
    </svg>
    <p class="kicker">AUSTRALIAN FABRICATION.</p>
    <h2 class="headline">Global Standards</h2>
  </section>

  <section class="banner banner--piping" aria-label="Piping Spools Fabrication banner">
    <svg viewBox="0 0 1040 148" width="1040" height="148" aria-hidden="true">
      <defs>
        <linearGradient id="piping-bg" x1="0" y1="0" x2="1" y2="1">
          <stop offset="0" stop-color="var(--brand-blue)"/>
          <stop offset="1" stop-color="var(--brand-blue-deep)"/>
        </linearGradient>
        <linearGradient id="pipework-photo" x1="0" y1="0" x2="1" y2="1">
          <stop offset="0" stop-color="var(--steel-light)"/>
          <stop offset="0.6" stop-color="var(--steel-mid)"/>
          <stop offset="1" stop-color="var(--steel-dark)"/>
        </linearGradient>
        <linearGradient id="tubes-photo" x1="0" y1="0" x2="1" y2="1">
          <stop offset="0" stop-color="#3d4550"/>
          <stop offset="0.5" stop-color="var(--steel-mid)"/>
          <stop offset="1" stop-color="#2f353d"/>
        </linearGradient>
      </defs>
      <rect class="banner-field" width="1040" height="148" fill="url(#piping-bg)"/>
      <polygon class="photo-area" points="0,0 232,0 210,148 0,148" fill="url(#pipework-photo)"
               role="img" aria-label="Photo of stainless steel process pipework with valves"/>
      <polygon class="divider-stripe" points="238,0 247,0 225,148 216,148" fill="#ffffff"/>
      <polygon class="divider-stripe" points="877,0 886,0 864,148 855,148" fill="#ffffff"/>
      <polygon class="photo-area" points="892,0 1040,0 1040,148 870,148" fill="url(#tubes-photo)"
               role="img" aria-label="Photo of polished steel tube sections"/>
    </svg>
    <p class="kicker">ENGINEERED FOR FLOW</p>
    <h2 class="headline">Built for Strength</h2>
  </section>

</main>
</body>
</html>
```